Business Card- Can you make it cool vs boring!

Need a refresh on my business card! Want it to be modern but simple, classic and a pop of coolness! we do senior living and it is boring. but that doesn't mean our business card have to look boring! Open to two sided cards. our website is www.Dunmere-PK.com

Target Market(s)

capital market

Industry/Entity Type

senior housing/ real estate

Contact Information for Business Card

logo/ name/ cell/ address/ www.Dunmere-PK.com/ space for a QR code

Requirements
Must have
• maybe a QR code (do not make prominent I may not use the QR so design where it can be taken out) that link to more about us/ landing page. needs to be modern but clean
Should not have
• clip art or script

```html
<!DOCTYPE html>
<html lang="en">
<head>
<meta charset="utf-8">
<title>Dunmere Living – Business Card</title>
<link href="https://fonts.googleapis.com/css2?family=Arimo:wght@400;700&display=swap" rel="stylesheet">
<style>
  :root {
    --rust: #a44b25;
    --rust-light: #ad552c;
    --steel: #7d7d7d;
    --ink: #4d4d4d;
    --paper: #ffffff;
    --backdrop: #f3f3f1;
  }
  * { box-sizing: border-box; margin: 0; padding: 0; }
  html, body { width: 1200px; height: 800px; overflow: hidden; }
  body {
    background: var(--backdrop);
    font-family: "Arimo", Arial, sans-serif;
    position: relative;
  }
  .card {
    position: absolute;
    top: 252px;
    width: 525px;
    height: 300px;
    box-shadow: 0 2px 10px rgba(0,0,0,0.12);
    overflow: hidden;
  }
  .card--front { left: 50px; background: var(--paper); }
  .card--back {
    left: 625px;
    background: linear-gradient(135deg, var(--rust), var(--rust-light));
    display: flex; align-items: center; justify-content: center;
  }

  .wordmark { text-align: center; line-height: 1; }
  .wordmark__name { font-size: 50px; font-weight: 400; letter-spacing: 1px; }
  .wordmark__tag {
    font-size: 13px; font-weight: 400; letter-spacing: 9px;
    margin-top: 8px; padding-left: 9px;
  }
  .card--back .wordmark { color: var(--paper); }
  .card--front .wordmark { color: var(--rust); position: absolute; top: 34px; left: 190px; }
  .card--front .wordmark__name { font-size: 46px; }

  .wave { position: absolute; left: 0; bottom: 0; width: 525px; height: 300px; }

  .holder {
    position: absolute; top: 132px; left: 40px; width: 190px; text-align: right;
  }
  .holder__name { color: var(--rust); font-weight: 700; font-size: 17px; letter-spacing: 0.3px; }
  .holder__role { color: var(--ink); font-size: 12px; margin-top: 3px; }

  .divider {
    position: absolute; top: 130px; left: 246px; width: 1px; height: 92px; background: var(--rust);
  }

  .contact {
    position: absolute; top: 130px; left: 262px; list-style: none;
    color: var(--ink); font-size: 13px; line-height: 18px;
  }
  .contact li { display: flex; align-items: center; gap: 6px; }
  .contact li.contact__address { display: block; padding-left: 16px; margin-bottom: 2px; }
  .contact svg { width: 10px; height: 10px; flex: none; }
  .contact .web { color: var(--rust); }
</style>
</head>
<body>

  <section class="card card--front" aria-label="Card front">
    <svg class="wave" viewBox="0 0 525 300" aria-hidden="true">
      <path d="M0 168 C 120 180, 170 250, 290 270 C 380 286, 460 282, 525 280 L525 300 L0 300 Z" fill="var(--steel)"/>
      <path d="M0 178 C 120 190, 170 258, 290 278 C 380 292, 460 290, 525 288 L525 300 L0 300 Z" fill="var(--paper)"/>
      <path d="M0 184 C 120 196, 170 264, 290 284 C 380 296, 460 296, 525 294 L525 300 L0 300 Z" fill="var(--rust)"/>
      <path d="M0 184 L0 300 L525 300 L525 294 C 400 298, 330 296, 270 290 C 170 280, 110 200, 0 184 Z" fill="var(--rust)"/>
    </svg>

    <div class="wordmark">
      <div class="wordmark__name">Dunmere</div>
      <div class="wordmark__tag">LIVING</div>
    </div>

    <div class="holder">
      <p class="holder__name">MARK ELLISON</p>
      <p class="holder__role">OWNER</p>
    </div>

    <div class="divider"></div>

    <ul class="contact">
      <li class="contact__address">4870 Birchwood Lane,<br>Suite #310</li>
      <li>
        <svg viewBox="0 0 10 10" aria-hidden="true"><path d="M2 0.5 L3.6 2.6 L2.7 3.6 C3.3 5 4.9 6.7 6.4 7.3 L7.4 6.4 L9.5 8 L8.4 9.5 C4.5 9.2 0.8 5.5 0.5 1.6 Z" fill="var(--rust)"/></svg>
        <span>(555) 204-7731</span>
      </li>
      <li>
        <svg viewBox="0 0 10 10" aria-hidden="true"><rect x="0.5" y="2" width="9" height="6" fill="none" stroke="var(--rust)"/><path d="M0.5 2 L5 5.5 L9.5 2" fill="none" stroke="var(--rust)"/></svg>
        <span>hello@Dunmere-PK.com</span>
      </li>
      <li>
        <svg viewBox="0 0 10 10" aria-hidden="true"><circle cx="5" cy="5" r="4.5" fill="none" stroke="var(--rust)"/><ellipse cx="5" cy="5" rx="2" ry="4.5" fill="none" stroke="var(--rust)"/><path d="M0.5 5 H9.5" stroke="var(--rust)"/></svg>
        <span>www.<span class="web">Dunmere-PK</span>.com</span>
      </li>
    </ul>
  </section>

  <section class="card card--back" aria-label="Card back">
    <div class="wordmark">
      <div class="wordmark__name">Dunmere</div>
      <div class="wordmark__tag">LIVING</div>
    </div>
  </section>

</body>
</html>
```